Custom Wordpress Theme - Original and Professional

We are a boutique IT consulting firm that provide small and medium business in Australia three different levels of IT service.
We are looking for a developer who will create a customised, original and professional wordpress theme. We are looking for the developer to create a professional, clean, clear and simple theme with a stylish layout, images and icons.
Our three services are: IT support | IT Services | IT Solutions and we would like to clearly differentiate the difference in each level of service in as few words as possible.
IT Support is the ad hock “call us, when you need us” service, that smaller business or those with minimal issues use.
IT service is the unlimited service, that business with existing (and well maintained) IT systems choose and is both flexible and scalable including no contracts or paperwork required.
IT solutions are the unlimited service that businesses that need new or updated infrastructure choose and it includes all the hardware, software and services with no contracts or any ongoing commitment.
The main page on the web site will attract the visitor to choose the right “service level” for their business and then we will have a dedicated page for each service and another page for a comparison (table) to compare all three services.
Lastly we will need a contact us page that has both office locations (Sydney and Melbourne), contact phone numbers and an email form.
Items we are focused on for this project are: 1. Images, 2.Icons 3. Layout.
In summary we are looking for a custom WordPress theme into a 6 page (Home, IT Support, IT Services, IT Solutions, Compare Service levels and Contact us) website. The design must include relevant images and icons and be clear, simple, professional and sleek.

Thank you for your time and creativity and I look forward to working with you!

Target Market(s)

Small and Medium businesses in Australia

Industry/Entity Type

Boutique

Requirements
Must have
• - 6 Pages layout: Home, IT support, IT services, IT Solutions, Compare service levels and Contact us
- Images, Layout and Icons.
- Clean, Clear, Simple, Elegant, Stylish.
Nice to have
• - Some text (if possible but not required).
Should not have
• - Complexity.
- Confusing layout.
- Generic non matching images and icons.

```html
<!DOCTYPE html>
<html lang="en">
<head>
<meta charset="utf-8">
<title>Harbourline – IT Support</title>
<link rel="stylesheet" href="https://fonts.googleapis.com/css2?family=PT+Sans+Narrow:wght@700&family=Source+Sans+3:wght@400;600&display=swap">
<style>
  :root {
    --blue: #1a73d9;
    --ink: #333333;
    --text: #3f3f3f;
    --line: #dcdcdc;
    --green: #7cc242;
    --footer-bg: #dcdad9;
    --white: #ffffff;
  }
  * { margin: 0; padding: 0; box-sizing: border-box; }
  html, body { width: 1200px; height: 1100px; overflow: hidden; background: var(--white); }
  body { position: relative; font-family: "Source Sans 3", Arial, sans-serif; color: var(--text); }

  .site-header { position: absolute; top: 0; left: 0; width: 1200px; height: 92px; }
  .brand { position: absolute; left: 121px; top: 26px; font-size: 30px; font-weight: 600; color: var(--blue); letter-spacing: -0.5px; }
  .main-nav { position: absolute; right: 129px; top: 40px; display: flex; gap: 37px; }
  .main-nav a { font-size: 14px; font-weight: 600; color: var(--ink); text-decoration: none; text-transform: uppercase; }
  .main-nav a.is-current { color: var(--blue); }

  .hero { position: absolute; top: 92px; left: 0; width: 1200px; height: 400px;
    background: linear-gradient(90deg, #3a3d42 0%, #6b5f5a 30%, #9a8476 55%, #c9a08a 75%, #e2bfa8 100%); }
  .hero-caption { position: absolute; left: 119px; top: 152px; width: 242px; height: 90px; background: rgba(255,255,255,0.94); padding: 0 8px; }
  .hero-title { font-family: "PT Sans Narrow", sans-serif; font-weight: 700; font-size: 54px; line-height: 56px; color: var(--blue); }
  .hero-tagline { font-family: "PT Sans Narrow", sans-serif; font-weight: 700; font-size: 23px; line-height: 24px; color: #111; margin-top: -2px; }
  .slider-dots { position: absolute; left: 120px; top: 356px; display: flex; gap: 5px; }
  .slider-dots span { width: 10px; height: 10px; border-radius: 50%; background: #9a9a9a; border: 1px solid #777; }
  .slider-dots span.is-active { background: #d8d8d8; }

  .service-card { position: absolute; top: 512px; width: 300px; height: 160px; border: 1px solid var(--line); text-align: center; }
  .service-card svg { position: absolute; left: 50%; top: 20px; transform: translateX(-50%); }
  .service-title { position: absolute; top: 63px; width: 100%; font-size: 19px; font-weight: 400; color: var(--ink); text-transform: uppercase; }
  .service-text { position: absolute; top: 94px; left: 12px; right: 12px; font-size: 13px; line-height: 17px; }

  .welcome-title { position: absolute; left: 121px; top: 701px; font-size: 18px; font-weight: 600; color: #555; text-transform: uppercase; }
  .welcome-photo { position: absolute; left: 119px; top: 742px; width: 389px; height: 220px;
    background: linear-gradient(135deg, #5b4a40 0%, #b8a79a 40%, #e6e2e0 55%, #2e3038 100%); }
  .welcome-body { position: absolute; left: 530px; top: 742px; width: 550px; font-size: 13px; line-height: 17px; text-align: justify; }
  .welcome-body p + p { margin-top: 17px; }
  .read-more { position: absolute; left: 120px; top: 976px; width: 87px; height: 30px; background: var(--green); color: var(--white);
    font-size: 12px; font-weight: 600; line-height: 30px; text-align: center; text-transform: uppercase; text-decoration: none; }

  .site-footer { position: absolute; top: 1040px; left: 0; width: 1200px; height: 60px; background: var(--footer-bg); }
  .copyright { position: absolute; left: 121px; top: 24px; font-size: 11px; color: #444; }
  .social-links { position: absolute; left: 908px; top: 17px; display: flex; gap: 7px; }
  .social-links span { width: 28px; height: 28px; background: #7a7a7a; }
</style>
</head>
<body>
  <header class="site-header">
    <div class="brand">Harbourline</div>
    <nav class="main-nav">
      <a class="is-current" href="#">Home</a>
      <a href="#">IT Support</a>
      <a href="#">IT Services</a>
      <a href="#">IT Solutions</a>
      <a href="#">Compare Service Levels</a>
      <a href="#">Contact Us</a>
    </nav>
  </header>

  <section class="hero" role="img" aria-label="Photo of a smiling support agent on the phone with colleagues blurred behind">
    <div class="hero-caption">
      <div class="hero-title">IT Support</div>
      <div class="hero-tagline">Call us, when you need us</div>
    </div>
    <div class="slider-dots"><span class="is-active"></span><span></span><span></span></div>
  </section>

  <article class="service-card" style="left:120px">
    <svg width="30" height="28" viewBox="0 0 30 28" aria-hidden="true">
      <path d="M4 18 V14 A11 11 0 0 1 26 14 V18" fill="none" stroke="#333" stroke-width="2.5"/>
      <rect x="2" y="15" width="6" height="11" rx="2" fill="#333"/>
      <rect x="22" y="15" width="6" height="11" rx="2" fill="#333"/>
    </svg>
    <h2 class="service-title">IT Support</h2>
    <p class="service-text">Sed ut perspiciatis unde omnis iste natus error sit voluptatem accusantium doloremque laudantium, totam rem aperiam, eaque ipsa quae ab illo</p>
  </article>

  <article class="service-card" style="left:450px">
    <svg width="36" height="36" viewBox="0 0 36 36" aria-hidden="true">
      <circle cx="14" cy="13" r="8" fill="none" stroke="#333" stroke-width="6" stroke-dasharray="4 2.3"/>
      <circle cx="14" cy="13" r="6" fill="#333"/>
      <circle cx="14" cy="13" r="3" fill="#fff"/>
      <circle cx="27" cy="28" r="4.5" fill="none" stroke="#333" stroke-width="3.5" stroke-dasharray="2.4 1.2"/>
      <circle cx="27" cy="28" r="1.5" fill="#fff"/>
    </svg>
    <h2 class="service-title">IT Services</h2>
    <p class="service-text">Sed ut perspiciatis unde omnis iste natus error sit voluptatem accusantium doloremque laudantium, totam rem aperiam, eaque ipsa quae ab illo</p>
  </article>

  <article class="service-card" style="left:780px">
    <svg width="20" height="34" viewBox="0 0 20 34" aria-hidden="true">
      <path d="M10 2 A8 8 0 0 1 18 10 C18 15 14 17 14 22 H6 C6 17 2 15 2 10 A8 8 0 0 1 10 2 Z" fill="#333"/>
      <rect x="6" y="24" width="8" height="2.5" fill="#333"/>
      <rect x="6" y="28" width="8" height="2.5" fill="#333"/>
      <rect x="8" y="31" width="4" height="2" fill="#333"/>
    </svg>
    <h2 class="service-title">IT Solutions</h2>
    <p class="service-text">Sed ut perspiciatis unde omnis iste natus error sit voluptatem accusantium doloremque laudantium, totam rem aperiam, eaque ipsa quae ab illo</p>
  </article>

  <h2 class="welcome-title">Welcome!</h2>
  <div class="welcome-photo" role="img" aria-label="Photo of a smiling business team gathered around a laptop"></div>
  <div class="welcome-body">
    <p>Sed ut perspiciatis unde omnis iste natus error sit voluptatem accusantium doloremque laudantium, totam rem aperiam, eaque ipsa quae ab illo inventore veritatis et quasi architecto beatae vitae dicta sunt explicabo. Nemo enim ipsam voluptatem quia voluptas sit aspernatur aut odit aut fugit, sed quia consequuntur magni dolores eos qui ratione voluptatem sequi nesciunt.</p>
    <p>Neque porro quisquam est, qui dolorem ipsum quia dolor sit amet, consectetur, adipisci velit, sed quia non numquam eius modi tempora incidunt ut labore et dolore magnam aliquam quaerat voluptatem. Ut enim ad minima veniam, quis nostrum exercitationem ullam corporis suscipit laboriosam, nisi ut aliquid ex ea commodi consequatur? Quis autem vel eum iure reprehenderit Ut enim ad minima veniam, quis nostrum exercitationem ullam corporis suscipit laboriosam, nisi ut aliquid ex ea commodi consequatur? Quis autem vel eum iure reprehenderit Ut enim ad minima veniam, quis nostrum exercitationem ullam corporis suscipit laboriosam, nisi ut aliquid ex ea commodi consequatur? Quis autem vel eum iure reprehenderit</p>
  </div>
  <a class="read-more" href="#">Read More</a>

  <footer class="site-footer">
    <p class="copyright">© 2000 - 2013 Kestrel Bay Consulting. All rights reserved.</p>
    <div class="social-links" aria-label="Social media links">
      <span></span><span></span><span></span><span></span><span></span>
    </div>
  </footer>
</body>
</html>
```